Las Vegas transportation company needs a dynamic design for business cards

We are a transportation management company based in Las Vegas specializing in operating and maintaining public transit systems. We want to keep our existing logo but would like to design business cards that feature one or more transit systems (e.g. monorail, train, bus) and maybe also the Las Vegas landscape.

```html
<!DOCTYPE html>
<html lang="en">
<head>
<meta charset="utf-8">
<title>Meridian Transit Group – Business Card</title>
<link href="https://fonts.googleapis.com/css2?family=Montserrat:wght@400;500;600;700&display=swap" rel="stylesheet">
<style>
  :root {
    --backdrop: #b5b5b5;
    --navy: #1b2557;
    --sky: #7fa6d8;
    --paper: #efeef3;
    --ink-soft: #4a4d5c;
    --white: #ffffff;
  }
  * { margin: 0; padding: 0; box-sizing: border-box; }
  html, body { width: 1200px; height: 900px; overflow: hidden; }
  body {
    position: relative;
    background: var(--backdrop);
    font-family: "Montserrat", Arial, sans-serif;
  }
  .card {
    position: absolute;
    left: 363px;
    width: 475px;
    height: 271px;
    overflow: hidden;
  }
  .card--front {
    top: 145px;
    background: var(--navy);
    display: flex;
    align-items: center;
    justify-content: center;
  }
  .front-name {
    color: var(--white);
    font-weight: 500;
    font-size: 22px;
    letter-spacing: 1px;
    text-align: center;
    line-height: 1.25;
  }
  .card--back {
    top: 484px;
    background: var(--paper);
  }
  .back-name {
    position: absolute;
    left: 41px;
    top: 54px;
    width: 140px;
    color: var(--navy);
    font-weight: 600;
    font-size: 16px;
    line-height: 1.2;
    letter-spacing: 0.3px;
  }
  .person {
    position: absolute;
    left: 41px;
    top: 130px;
  }
  .person__name {
    color: var(--navy);
    font-weight: 700;
    font-size: 16px;
    line-height: 1.1;
  }
  .person__role {
    color: var(--ink-soft);
    font-size: 11px;
    line-height: 1.3;
  }
  .contacts {
    position: absolute;
    left: 41px;
    top: 174px;
    list-style: none;
  }
  .contacts li {
    display: flex;
    align-items: center;
    gap: 7px;
    color: var(--ink-soft);
    font-size: 10.5px;
    line-height: 14px;
  }
  .contacts svg { width: 10px; height: 10px; flex: none; }
  .photo-panel {
    position: absolute;
    left: 195px;
    top: 0;
    width: 280px;
    height: 175px;
    border-bottom-left-radius: 60px;
    background: linear-gradient(110deg, #5a8fcf 0%, #c9d3de 30%, #f1cc1d 52%, #2f9b52 66%, #3c4fb0 80%, #c8377d 100%);
  }
  .address-band {
    position: absolute;
    left: 0;
    top: 234px;
    width: 100%;
    height: 17px;
    display: flex;
  }
  .address-band__main {
    width: 411px;
    background: var(--navy);
    color: var(--white);
    font-size: 10.5px;
    line-height: 17px;
    padding-left: 40px;
  }
  .address-band__accent { flex: 1; background: var(--sky); }
</style>
</head>
<body>
  <section class="card card--front">
    <span class="front-name">Meridian Transit Group</span>
  </section>

  <section class="card card--back">
    <div class="photo-panel" role="img" aria-label="Motion-blurred photo of a monorail and Las Vegas transit vehicles"></div>

    <div class="back-name">Meridian<br>Transit Group</div>

    <div class="person">
      <div class="person__name">Dana Whitfield</div>
      <div class="person__role">President &amp; CEO</div>
    </div>

    <ul class="contacts">
      <li>
        <svg viewBox="0 0 10 10" aria-hidden="true"><path d="M2 1l2 2-1 1c.5 1.2 1.6 2.3 3 3l1-1 2 2-1.2 1.2C4.5 9 1 5.5.8 2.2z" fill="var(--navy)"/></svg>
        (702) 555-0147
      </li>
      <li>
        <svg viewBox="0 0 10 10" aria-hidden="true"><rect x="0.5" y="2" width="9" height="6" fill="var(--navy)"/><path d="M0.5 2l4.5 3.5L9.5 2" stroke="var(--paper)" stroke-width="0.9" fill="none"/></svg>
        info@meridiantransit.com
      </li>
      <li>
        <svg viewBox="0 0 10 10" aria-hidden="true"><g fill="none" stroke="var(--navy)" stroke-width="0.9"><circle cx="5" cy="5" r="4.2"/><ellipse cx="5" cy="5" rx="1.8" ry="4.2"/><path d="M0.8 5h8.4M1.5 3h7M1.5 7h7"/></g></svg>
        www.meridiantransit.com
      </li>
    </ul>

    <div class="address-band">
      <div class="address-band__main">P.O Box 40210 | Las Vegas, NV 89101</div>
      <div class="address-band__accent"></div>
    </div>
  </section>
</body>
</html>
```